BRAMBLEFORD CONSTRUCTIONS B-Card

I currently have a b-card design but will be removing the image (tree) from the logo and have text only.
I want the card to be classy and strong within the building and construction industry.
I will be using Spot UV on the cards as per the attached examples. I will also send through some sketched ideas that I have in mind.
The color blue is similar to the image (No. 6) attached images

Target Market(s)

middle to maturre aged.
Home Owners / Renovators and Builders

Industry/Entity Type

Construction

Contact Information for Business Card

BRAMBLEFORD CONSTRUCTIONS
Name: Gareth Pennick
Title: Project Manager
Mobile: 0427 351 804
Office: (08) 9316 5172
Address: 47C Corvell Street, Malaga WA 6090
Email: info@bramblefordhomes.com.au
PO Box: 3817 Malaga WA 6944

Colors
0592cd
33a6d7
85cae6
1b1b1b

Requirements
Must have
• 1. It must have spot UV on the front of card, maybe back of card too
• 2. I really like the blue on image 6. (or at least a really cool electric blue against the charcoal grey background)
• 3. The font must be slimline and modern. Easy to read
• 4. There must be no black used on the card... Only greys and dark charcoal greys
• 5. Use only the text from the logo "Brambleford Constructions" Not the image of the tree. I am wanting the b-cards to be more masculine.
Nice to have
• 1. I like the design concept on image 6. but happy to see what else you can do with the Spot UV
• 2. Unless you have a really cool idea of the image of the tree (from previous logo) Spot UV somewhere in the design concept thats original and different then I am keen to see what you come up with
• 3. Try changing the color of the logo eg. full white or Blue and white
• 4. Another option is to have the Brambleford Logo on the front of card with the spot UV in the background of text which we specialise in eg, Roofing, Ceiling, Insulation, Gutter Guards, Electrical, Insurance etc and we can add or reduce items as required. Similar to image 12.
Should not have
• Do not include the image of the tree from previous logo. unless you have a really cool idea of Spot UV somewhere in the design concept thats original and different.

```html
<!DOCTYPE html>
<html lang="en">
<head>
<meta charset="utf-8">
<title>Brambleford Constructions – Business Card</title>
<link rel="stylesheet" href="https://fonts.googleapis.com/css2?family=Source+Sans+3:wght@400;600&display=swap">
<style>
  :root {
    --backdrop: #e9e6e2;
    --charcoal: #242425;
    --charcoal-pattern-a: #2e2e30;
    --charcoal-pattern-b: #1f1f20;
    --blue: #33a6d7;
    --blue-deep: #0592cd;
    --white: #f4f4f4;
    --grey-text: #d8d8d8;
    --divider: #4a4a4c;
  }
  * { box-sizing: border-box; margin: 0; padding: 0; }
  html, body {
    width: 1200px;
    height: 900px;
    overflow: hidden;
    background: var(--backdrop);
    font-family: "Source Sans 3", "Myriad Pro", Arial, sans-serif;
  }
  .stage {
    position: relative;
    width: 1200px;
    height: 900px;
  }
  .card {
    position: absolute;
    width: 540px;
    height: 330px;
    background: var(--charcoal);
    border-radius: 3px;
    box-shadow: 0 10px 28px rgba(0, 0, 0, 0.22);
    overflow: hidden;
  }
  .card--back { left: 90px; top: 110px; }
  .card--front { left: 570px; top: 460px; }

  .pattern-field {
    position: absolute;
    inset: 0;
    background: radial-gradient(circle at 30% 40%, var(--charcoal-pattern-a), var(--charcoal-pattern-b) 75%);
  }

  .wordmark {
    position: absolute;
    left: 0;
    right: 0;
    text-align: center;
    font-weight: 600;
    line-height: 1;
  }
  .wordmark__line { display: block; }
  .wordmark__primary { font-size: 46px; letter-spacing: 1px; }
  .wordmark__secondary { font-size: 20px; letter-spacing: 10px; margin-top: 6px; padding-left: 10px; }

  .card--back .wordmark { top: 118px; color: var(--white); }
  .card--front .wordmark { top: 62px; color: var(--blue); }

  .contact {
    position: absolute;
    left: 0;
    right: 0;
    top: 194px;
    display: flex;
    justify-content: center;
    align-items: center;
    gap: 14px;
  }
  .contact__person { text-align: right; }
  .contact__name {
    color: var(--blue);
    font-weight: 600;
    font-size: 18px;
    line-height: 1.1;
  }
  .contact__title {
    color: var(--grey-text);
    font-size: 14px;
    line-height: 1.3;
  }
  .contact__divider {
    width: 1px;
    height: 42px;
    background: var(--divider);
  }
  .contact__phones { list-style: none; }
  .contact__phone {
    display: flex;
    align-items: center;
    gap: 6px;
    color: var(--grey-text);
    font-size: 14px;
    line-height: 1.45;
  }
  .contact__icon { width: 11px; height: 11px; flex: none; }

  .address {
    position: absolute;
    left: 0;
    right: 0;
    top: 260px;
    text-align: center;
    color: var(--grey-text);
    font-size: 14.5px;
    line-height: 1.4;
  }
  .address__label { font-weight: 600; color: var(--white); }
</style>
</head>
<body>
<main class="stage">

  <section class="card card--back" aria-label="Business card back">
    <div class="pattern-field" role="img" aria-label="Tone-on-tone spot UV pattern of repeated tree motifs across the card"></div>
    <p class="wordmark">
      <span class="wordmark__line wordmark__primary">BRAMBLEFORD</span>
      <span class="wordmark__line wordmark__secondary">CONSTRUCTIONS</span>
    </p>
  </section>

  <section class="card card--front" aria-label="Business card front">
    <p class="wordmark">
      <span class="wordmark__line wordmark__primary">BRAMBLEFORD</span>
      <span class="wordmark__line wordmark__secondary">CONSTRUCTIONS</span>
    </p>

    <div class="contact">
      <div class="contact__person">
        <p class="contact__name">Gareth Pennick</p>
        <p class="contact__title">Project Manager</p>
      </div>
      <span class="contact__divider"></span>
      <ul class="contact__phones">
        <li class="contact__phone">
          <svg class="contact__icon" viewBox="0 0 12 12" aria-hidden="true">
            <rect x="3" y="0.5" width="6" height="11" rx="1.2" fill="none" stroke="#33a6d7" stroke-width="1.2"/>
            <circle cx="6" cy="9.6" r="0.7" fill="#33a6d7"/>
          </svg>
          0427 351 804
        </li>
        <li class="contact__phone">
          <svg class="contact__icon" viewBox="0 0 12 12" aria-hidden="true">
            <path d="M1 4.2C1 2.6 3.3 1.5 6 1.5s5 1.1 5 2.7v0.9H8.4V3.8H3.6v1.3H1z" fill="#33a6d7"/>
            <rect x="2.2" y="6" width="7.6" height="5" rx="1" fill="#33a6d7"/>
          </svg>
          (08) 9316 5172
        </li>
      </ul>
    </div>

    <p class="address">
      47C Corvell Street, Kellerton WA 6071<br>
      <span class="address__label">PO Box:</span> 3817 Kellerton WA 6932
    </p>
  </section>

</main>
</body>
</html>
```